Hollow Thicket, a 3d voxel survival video game needs a card for gaming conventions

I am the lead developer for Hollow Thicket http://www.HollowThicket.example and need a business card to hand out at an indie gaming convention
The card would need to include the game name, website url, my name, position (Lead Developer), e-mail and phone number
The game is a 3d, voxel (with smooth terrain) based survival game with guns and wildlife. The main icon of the game would likely be a grizzly bear but I am willing to accept other designs too.
Attached is a media kit for the game with some images you can use but don't have to its just what little art I can provide. Anything on the website or from the video game can also be used. unrelated art can also be used.
Target Market(s)
Indie Developers/publishers at conferences
Industry/Entity Type
Games
Contact Information for Business Card
Name: Corin Waldrick
Position: Lead Developer
E-mail: Pale_Kettle@mailbox.example
Phone number: 555-372-1186

```html
<!DOCTYPE html>
<html lang="en">
<head>
<meta charset="utf-8">
<title>Hollow Thicket – Business Card</title>
<link rel="stylesheet" href="https://fonts.googleapis.com/css2?family=Open+Sans:wght@400;600;700&display=swap">
<style>
  :root {
    --stage: #e9e6e2;
    --card-white: #ffffff;
    --band-top: #a3190c;
    --band-bottom: #a48b52;
    --ink-light: #ffffff;
    --brand-ink: #f3e6c8;
    --bear-dark: #3b2a1c;
    --bear-mid: #6b4e33;
    --bear-light: #8f7150;
    --card-shadow: rgba(0, 0, 0, 0.25);
  }
  html, body {
    margin: 0;
    padding: 0;
    width: 1200px;
    height: 900px;
    overflow: hidden;
    background: var(--stage);
    font-family: "Open Sans", Arial, sans-serif;
  }
  .canvas {
    position: relative;
    width: 1200px;
    height: 900px;
  }
  .card {
    position: absolute;
    background: var(--card-white);
    overflow: hidden;
    box-shadow: 0 6px 18px var(--card-shadow);
  }
  .card--front { left: 77px; top: 34px; width: 590px; height: 365px; }
  .card--back  { left: 388px; top: 505px; width: 567px; height: 352px; }

  .band {
    position: absolute;
    left: 0;
    right: 0;
    bottom: 0;
    background: linear-gradient(to bottom, var(--band-top), var(--band-bottom));
  }
  .card--front .band { top: 133px; }
  .card--back .band  { top: 131px; }

  .bear-art {
    position: absolute;
    background: radial-gradient(ellipse at 40% 35%, var(--bear-light), var(--bear-mid) 45%, var(--bear-dark) 100%);
    border-radius: 46% 40% 0 0 / 40% 36% 0 0;
    filter: drop-shadow(0 0 8px rgba(0,0,0,0.35));
  }
  .card--front .bear-art { left: 321px; top: 128px; width: 268px; height: 237px; }
  .card--back .bear-art  { left: 0; top: 127px; width: 192px; height: 225px; border-radius: 40% 46% 0 0 / 36% 40% 0 0; }

  .contact-block {
    position: absolute;
    left: 31px;
    top: 192px;
    width: 290px;
    color: var(--ink-light);
  }
  .holder-name {
    margin: 0;
    font-size: 20px;
    font-weight: 700;
    line-height: 1.2;
  }
  .holder-role {
    margin: 0;
    font-size: 16px;
    font-weight: 400;
    line-height: 1.3;
  }
  .contact-list {
    list-style: none;
    margin: 36px 0 0;
    padding: 0;
    font-size: 16px;
    line-height: 23px;
  }
  .contact-list li {
    display: flex;
    align-items: center;
    gap: 9px;
    white-space: nowrap;
  }
  .contact-icon {
    width: 13px;
    height: 13px;
    fill: var(--ink-light);
    flex: none;
  }

  .game-name {
    position: absolute;
    left: 225px;
    top: 190px;
    width: 310px;
    margin: 0;
    text-align: center;
    font-size: 38px;
    font-weight: 700;
    line-height: 1.05;
    letter-spacing: 2px;
    color: var(--brand-ink);
    text-transform: uppercase;
  }
</style>
</head>
<body>
<main class="canvas">

  <section class="card card--front" aria-label="Card front">
    <div class="band"></div>
    <div class="bear-art" role="img" aria-label="Photograph of a roaring grizzly bear"></div>
    <div class="contact-block">
      <p class="holder-name">Corin Waldrick</p>
      <p class="holder-role">Lead Developer</p>
      <ul class="contact-list">
        <li>
          <svg class="contact-icon" viewBox="0 0 24 24" aria-hidden="true"><path d="M6.6 10.8a15.1 15.1 0 0 0 6.6 6.6l2.2-2.2c.3-.3.7-.4 1-.2 1.1.4 2.3.6 3.6.6.6 0 1 .4 1 1V20c0 .6-.4 1-1 1A17 17 0 0 1 3 4c0-.6.4-1 1-1h3.5c.6 0 1 .4 1 1 0 1.3.2 2.5.6 3.6.1.3 0 .7-.2 1z"/></svg>
          <span>555-372-1186</span>
        </li>
        <li>
          <svg class="contact-icon" viewBox="0 0 24 24" aria-hidden="true"><path d="M2 6l10 7.5L22 6v13H2z"/><path d="M2 5h20l-10 7.5z"/></svg>
          <span>Pale_Kettle@mailbox.example</span>
        </li>
        <li>
          <svg class="contact-icon" viewBox="0 0 24 24" aria-hidden="true"><circle cx="12" cy="12" r="9" fill="none" stroke="#fff" stroke-width="2"/><path d="M3 12h18M12 3c3 3 3 15 0 18M12 3c-3 3-3 15 0 18" fill="none" stroke="#fff" stroke-width="2"/></svg>
          <span>www.HollowThicket.example</span>
        </li>
      </ul>
    </div>
  </section>

  <section class="card card--back" aria-label="Card back">
    <div class="band"></div>
    <div class="bear-art" role="img" aria-label="Photograph of a roaring grizzly bear"></div>
    <h1 class="game-name">Hollow<br>Thicket</h1>
  </section>

</main>
</body>
</html>
```